Spanish Student Needs a Cover for his PhD Dissertation

Hi everyone :) So, I'm a Corneal surgeon currently finishing my PhD, with a dissertation focused on the evaluation of quality of life in patients affected by a disease called Keratoconus. Just so you know, Keratoconus is a condition in which the cornea (the frontal part of the way) gets thin and bulgy and it decreases vision. What I did during my PhD was designing a questionnaire for evaluating quality of life in this kind of patients.
I need to design a hard cover for my dissertation, which is 200 sheets long. I like kind of minimalistic and geometric designs but I am totally open to suggestions. What needs to be in the cover is the name of the dissertation "Diseño, desarrollo y validación de una encuesta para evaluar el compromiso visual y emocional subjetivos en pacientes con Queratocono" and my name, "Iker Zurmendi". The other thing that needs to go there is the logo of my university (Universidad de Montehierro). Aside from that, anything else is up to the designer. It would be important to use the kind of "red" color I am using in the dissertation. I am attaching the frontal page of my dissertation so you know what kind of design and colors I am using.
In the back part, of the cover, there should be this small inscription: "Iker Zurmendi, MD, es un Oftalmólogo Subespecialista en Cirugía Refractiva de la Universidad Tecnológica Cordillerana (Colombia) y la Universidad de Montehierro (España). Actualmente se desempeña como miembro del Departamento de Córnea y Cirugía Refractiva de la Clínica de Oftalmología Miraluz y como director de su propia compañía de emprendimiento médico Silver Heron Surgical". Please leave a space to place my picture; I will have it taken this week so I don't have it right now, you can just leave the blank spot and I will include it later
The size of the pages is standard "letter" size.
Thanks a lot!

Target Market(s)

PhD Scholars

Font styles to use
Serif

Requirements
Must have
• The "red" color I use on my font. It must be formal but "young".
Nice to have
• I like to keep the design clean, kind of "formal with a young" touch so to speak. I really like gray colors, so it would be nice to have broad areas of gray. I love geometrical designs.
I have uploaded a very early version a friend of mine made (it even had a different title); this can be a starting point for you to work on, but I am more than open to suggestions and new ideas.
Should not have
• Please don't use my whole name, Iker Zurmendi is fine. I don't like ALL CAPITALS.

```html
<!DOCTYPE html>
<html lang="es">
<head>
<meta charset="utf-8">
<title>Cubierta de tesis doctoral – Queratocono</title>
<link rel="stylesheet" href="https://fonts.googleapis.com/css2?family=Cormorant+Garamond:wght@300;400;600;700&family=EB+Garamond:wght@400;500;600&display=swap">
<style>
  :root {
    --backdrop: #231f20;
    --cover-red: #c4161c;
    --paper: #ffffff;
    --ink: #231f20;
    --art-light: #8fd6f4;
    --art-mid: #3a94d8;
    --art-dark: #1a2f86;
  }
  * { margin: 0; padding: 0; box-sizing: border-box; }
  html, body { width: 1200px; height: 1200px; overflow: hidden; background: var(--backdrop); }
  .canvas { position: relative; width: 1200px; height: 1200px; }

  .cover { position: absolute; left: 51px; top: 253px; width: 1098px; height: 694px; overflow: hidden; }

  /* Back + spine */
  .back { position: absolute; left: 0; top: 0; width: 561px; height: 694px; background: var(--cover-red); color: var(--paper); font-family: "EB Garamond", serif; }
  .back-copy { position: absolute; left: 45px; top: 45px; width: 446px; font-size: 9.2px; line-height: 12.7px; text-align: justify; font-weight: 500; hyphens: auto; }
  .back-copy p + p { margin-top: 4px; }
  .author-photo { position: absolute; left: 208px; top: 359px; width: 119px; height: 119px; border-radius: 50%; background: var(--paper); display: flex; align-items: center; justify-content: center; color: var(--ink); font-size: 17px; }
  .author-bio { position: absolute; left: 45px; top: 497px; width: 446px; font-size: 9.2px; line-height: 12.7px; text-align: justify; font-weight: 500; }

  .spine-title { position: absolute; left: 545px; top: 196px; width: 14px; height: 244px; }
  .spine-title span { position: absolute; left: 0; top: 0; width: 244px; transform-origin: 0 0; transform: translateX(14px) rotate(90deg); font-size: 6.3px; line-height: 7px; text-align: center; }
  .spine-author { position: absolute; left: 542px; top: 591px; width: 14px; height: 70px; }
  .spine-author span { position: absolute; left: 0; top: 0; width: 70px; transform-origin: 0 0; transform: translateX(14px) rotate(90deg); font-size: 11px; white-space: nowrap; }

  /* Front */
  .front { position: absolute; left: 561px; top: 0; width: 537px; height: 694px; background: var(--paper); font-family: "Cormorant Garamond", serif; color: var(--ink); }
  .title-lead { position: absolute; left: 25px; top: 81px; font-size: 128px; line-height: 1; font-weight: 600; color: var(--cover-red); letter-spacing: -1px; }
  .eye-art { position: absolute; left: 316px; top: 56px; width: 180px; height: 180px; }
  .title-line { position: absolute; left: 27px; white-space: nowrap; line-height: 1.2; }
  .title-light { font-weight: 300; font-size: 36.5px; }
  .title-bold { font-weight: 700; font-size: 39px; }
  .line-1 { top: 206px; }
  .line-2 { top: 247px; }
  .line-3 { top: 293px; }
  .line-4 { top: 341px; font-size: 27.3px; }
  .title-disease { position: absolute; left: 25px; top: 367px; width: 490px; height: 95px; overflow: visible; }

  .university { position: absolute; left: 80px; width: 352px; top: 483px; text-align: center; }
  .university-mark { width: 74px; height: 74px; margin: 0 auto; border-radius: 50%; border: 2px solid var(--cover-red); }
  .university-name { margin-top: 4px; font-family: "EB Garamond", serif; font-weight: 600; font-size: 16px; color: var(--cover-red); }
  .author-name { position: absolute; left: 80px; width: 378px; top: 611px; text-align: center; font-size: 42px; font-weight: 400; letter-spacing: 1px; }
</style>
</head>
<body>
<div class="canvas">
  <div class="cover">
    <section class="back">
      <div class="back-copy">
        <p>Lorem ipsum dolor sit amet, consectetuer adipiscing elit, sed diam nonummy nibh euismod tincidunt ut laoreet dolore magna aliquam erat volutpat. Ut wisi enim ad minim veniam, quis nostrud exerci tation ullamcorper suscipit lobortis nisl ut aliquip ex ea commodo consequat. Duis autem vel eum iriure dolor in hendrerit in vulputate velit esse molestie consequat, vel illum dolore eu feugiat nulla facilisis at vero eros et accumsan et iusto odio dignissim qui blandit praesent luptatum zzril delenit augue duis dolore te feugait nulla facilisi.</p>
        <p>Lorem ipsum dolor sit amet, cons ectetuer adipiscing elit, sed diam nonummy nibh euismod tincidunt ut laoreet dolore magna aliquam erat volutpat. Ut wisi enim ad minim veniam, quis nostrud exerci tation ullamcorper suscipit lobortis nisl ut aliquip ex ea commodo consequat.</p>
        <p>Lorem ipsum dolor sit amet, consectetuer adipiscing elit, sed diam nonummy nibh euismod tincidunt ut laoreet dolore magna aliquam erat volutpat. Ut wisi enim ad minim veniam, quis nostrud exerci tation ullamcorper suscipit lobortis nisl ut aliquip ex ea commodo consequat. Duis autem vel eum iriure dolor in hendrerit in vulputate velit esse molestie consequat, vel illum dolore eu feugiat nulla facilisis at vero eros et accumsan et iusto odio dignissim qui blandit praesent luptatum zzril delenit augue duis dolore te feugait nulla facilisi.</p>
        <p>Lorem ipsum dolor sit amet, cons ectetuer adipiscing elit, sed diam nonummy nibh euismod tincidunt ut laoreet dolore magna aliquam erat volutpat. Ut wisi enim ad minim veniam, quis nostrud exerci tation ullamcorper suscipit lobortis nisl ut aliquip ex ea commodo consequat.</p>
        <p>Lorem ipsum dolor sit amet, consectetuer adipiscing elit, sed diam nonummy nibh euismod tincidunt ut laoreet dolore magna aliquam erat volutpat. Ut wisi enim ad minim veniam, quis nostrud exerci tation ullamcorper suscipit lobortis nisl ut aliquip ex ea commodo consequat. Duis autem vel eum iriure dolor in hendrerit in vulputate velit esse molestie consequat, vel illum dolore eu feugiat nulla facilisis at vero eros et accumsan et iusto odio dignissim qui blandit praesent luptatum zzril delenit augue duis dolore te feugait nulla facilisi.</p>
        <p>Lorem ipsum dolor sit amet, cons ectetuer adipiscing elit, sed diam nonummy nibh euismod tincidunt ut laoreet</p>
      </div>
      <div class="author-photo">authors photo</div>
      <p class="author-bio">Iker Zurmendi, MD, es un Oftalmólogo Subespecialista en Cirugía Refractiva de la Universidad Tecnológica Cordillerana (Colombia) y la Universidad de Montehierro (España). Actualmente se desempeña como miembro del Departamento de Córnea y Cirugía Refractiva de la Clínica de Oftalmología Miraluz y como director de su propia compañía de emprendimiento médico Silver Heron Surgical</p>
      <div class="spine-title"><span>Diseño, desarrollo y validación de una encuesta para evaluar el compromiso visual y emocional subjetivos en pacientes con Queratocono</span></div>
      <div class="spine-author"><span>Iker Zurmendi</span></div>
    </section>

    <section class="front">
      <div class="title-lead">Diseñ</div>
      <svg class="eye-art" viewBox="0 0 180 180" role="img" aria-label="Espacio para la ilustración circular de un ojo azul">
        <defs>
          <radialGradient id="art-fill" cx="50%" cy="50%" r="50%">
            <stop offset="0" stop-color="var(--art-light)"/>
            <stop offset="0.65" stop-color="var(--art-mid)"/>
            <stop offset="1" stop-color="var(--art-dark)"/>
          </radialGradient>
        </defs>
        <circle cx="90" cy="90" r="89" fill="url(#art-fill)"/>
      </svg>
      <div class="title-line title-light line-1">desarrollo y validación</div>
      <div class="title-line title-bold line-2">de una encuesta para</div>
      <div class="title-line title-bold line-3">evaluar el compromiso visual</div>
      <div class="title-line title-light line-4">y emocional subjetivos en pacientes con</div>
      <svg class="title-disease" viewBox="0 0 490 95">
        <text x="0" y="65" textLength="486" lengthAdjust="spacingAndGlyphs" font-family="Cormorant Garamond, serif" font-weight="600" font-size="72" fill="var(--cover-red)">QUERATOCONO</text>
      </svg>
      <div class="university">
        <div class="university-mark"></div>
        <div class="university-name">Universidad de Montehierro</div>
      </div>
      <div class="author-name">Iker Zurmendi</div>
    </section>
  </div>
</div>
</body>
</html>
```